Boutique custom software development company needs new business card

Our nearly 20 year old custom software development company would like to better include the fact that we are now providing Bitcoin services. These new services are B2B include education (how to acquire and securely hold Bitcoin) and integrating Bitcoin payments into existing ecommerce sites or other existing systems. Please keep the card clean and simple. Attached is our current design and some other files. vextorial.com

Target Market(s)

businesses owners interested in long term relationship

Industry/Entity Type

Custom software development and Bitcoin

Contact Information for Business Card

Dale Parker, dale@vextorial.com, vextorial.com, (888) 555-VXTRL

Font styles to use
Other font styles liked:
• monospace

Requirements
Must have
• double-sided
Nice to have
• clean and simple
Should not have
• physical address

```html
<!DOCTYPE html>
<html lang="en">
<head>
<meta charset="utf-8">
<title>Vextorial — Business Card</title>
<link rel="stylesheet" href="https://fonts.googleapis.com/css2?family=Montserrat:wght@400;800&family=Share+Tech+Mono&family=Source+Code+Pro:wght@500&display=swap">
<style>
  :root {
    --stage: #2a2a2a;
    --navy: #0b1437;
    --navy-deep: #07102e;
    --blue: #3a6bb5;
    --orange: #f07d22;
    --white: #ffffff;
  }
  * { box-sizing: border-box; margin: 0; padding: 0; }
  html, body {
    width: 1200px; height: 801px; overflow: hidden;
    background: var(--stage);
  }
  .stage {
    position: relative; width: 1200px; height: 801px;
    display: flex; align-items: center; justify-content: center; gap: 50px;
  }
  .card {
    position: relative; width: 520px; height: 297px;
    border-radius: 16px; overflow: hidden;
  }
  .card-front {
    background: var(--white);
    display: flex; align-items: center; justify-content: center;
  }
  .brand { display: flex; flex-direction: column; align-items: flex-start; }
  .brand-name {
    font-family: "Montserrat", sans-serif; font-weight: 800;
    text-transform: uppercase; letter-spacing: 1px; line-height: 1;
  }
  .brand-tagline {
    font-family: "Montserrat", sans-serif; font-weight: 400; line-height: 1.2;
  }
  .card-front .brand-name { color: var(--navy); font-size: 52px; }
  .card-front .brand-tagline { color: var(--navy); font-size: 19px; margin-top: 6px; padding-left: 4px; }

  .card-back {
    background: linear-gradient(90deg, var(--navy-deep) 0%, var(--navy) 62%, var(--blue) 100%);
  }
  .back-content {
    position: absolute; right: 34px; top: 52px;
    display: flex; flex-direction: column; align-items: flex-end;
  }
  .card-back .brand { align-items: flex-start; }
  .card-back .brand-name { color: var(--white); font-size: 30px; }
  .card-back .brand-tagline { color: var(--white); font-size: 11px; margin-top: 4px; }
  .holder-name {
    font-family: "Share Tech Mono", monospace; color: var(--orange);
    font-size: 27px; letter-spacing: 2px; text-transform: uppercase;
    margin-top: 22px;
  }
  .contact-list { list-style: none; margin-top: 12px; }
  .contact-item {
    display: flex; justify-content: flex-end; align-items: center; gap: 8px;
    font-family: "Source Code Pro", monospace; font-weight: 500;
    color: var(--white); font-size: 13px; line-height: 1.65;
  }
  .contact-icon { width: 11px; height: 11px; flex: none; }
</style>
</head>
<body>
<main class="stage">
  <section class="card card-front" aria-label="Card front">
    <div class="brand">
      <span class="brand-name">Vextorial</span>
      <span class="brand-tagline">developer of custom applications</span>
    </div>
  </section>

  <section class="card card-back" aria-label="Card back">
    <div class="back-content">
      <div class="brand">
        <span class="brand-name">Vextorial</span>
        <span class="brand-tagline">developer of custom applications</span>
      </div>
      <p class="holder-name">Dale Parker</p>
      <ul class="contact-list">
        <li class="contact-item">(888) 555-VXTRL
          <svg class="contact-icon" viewBox="0 0 12 12" aria-hidden="true"><path d="M2.5 1 L4.5 1 L5.2 3.6 L4 4.6 Q5 6.9 7.4 8 L8.4 6.8 L11 7.5 L11 9.5 Q11 11 9.5 11 Q1 10.4 1 2.5 Q1 1 2.5 1Z" fill="var(--orange)"/></svg>
        </li>
        <li class="contact-item">dale@vextorial.com
          <svg class="contact-icon" viewBox="0 0 12 12" aria-hidden="true"><rect x="0.5" y="2.5" width="11" height="7.5" fill="var(--orange)"/><path d="M0.5 2.5 L6 6.8 L11.5 2.5" fill="none" stroke="var(--navy)" stroke-width="1"/></svg>
        </li>
        <li class="contact-item">vextorial.com
          <svg class="contact-icon" viewBox="0 0 12 12" aria-hidden="true"><circle cx="6" cy="6" r="5" fill="none" stroke="var(--orange)" stroke-width="1.4"/><ellipse cx="6" cy="6" rx="2" ry="5" fill="none" stroke="var(--orange)" stroke-width="1"/><line x1="1" y1="6" x2="11" y2="6" stroke="var(--orange)" stroke-width="1"/></svg>
        </li>
      </ul>
    </div>
  </section>
</main>
</body>
</html>
```